Thornbury Spa

We are a large Miami Beach spa and salon. I am still building our website but you can use it as a resource to gain a better understanding of who we are ....www.velloraspa-studio.com.

We offer a comprehensive list of services in hair, nails, massage, skin care, tanning, spray tanning and waxing and we offer high quality products for skin care, tanning and hair. We are open 7 days.

We would like to see a clean and simple menu that looks a lot like the one from "The Spa at Larkwood." In particular, we have a copy of a menu from their West Hollywood, CA location that is just beautiful. In the uploaded content you will see a sampling of that menu. We would like to see greys, blacks, silvers, whites and warm colors like reds and oranges. We specifically attempt to remain gender neutral so that we don't attract only girls (with pink colors and flowers etc). The final design should convey a simple, clean, friendly environment and the final product should be sized such that it is 1.) portable and 2.) inexpensive to print. We will be running thousands of these at a time so cost of printing is a consideration.

The booklet consists of two parts: one part is the standard menu with descriptions of services and products and photos etc (think of this as the sales piece that convinces a potential customer to visit) and will be stapled together like you would expect a small menu to be and should resemble the Larkwood menu. The prices should not be included in this part of the booklet that will be printed and stapled. The other part is a single insert and is removable and replaceable. I want this removable insert placed in the last page of the book in a folder pocket or something else that you can think of so that when it's time to change prices here that I am not throwing away all of the booklets....I am only replacing the inserts at the end of the menu booklet. Please design this single page insert so that should a customer remove it from the booklet and keep it, that it stands alone with our name, logo, website and phone number. This page can and probably will have to be 2 sided.

At the back of the booklet, I also want the polices to be printed in one page (think fine print in any sort of business dealing.)

With regard to the look and feel slider of economical v upmarket...we definitely want to convey we deliver upmarket services at reasonable prices. Think, world class services and products at reasonable, everyday prices.

With regard to the uploaded files:
I uploaded both EPS and TIF formats. The colors in those files are not the palette we want at all. The colors we want use for the circular logo must match the standard colors as depicted in the uploaded file "Thornburytanrooms"

Target Market(s)

The target market is the average 20-35 year old in Miami Beach that cares about their appearance. The range of clientele is quite diverse.

Industry/Entity Type

Environment

Requirements
Must have
• It must have elegant and simple photographs that relate to the services being offered. We are selling a service set and an environment...so this menu should be reflect that goal. The logo should be repeated often throughout the book but in subtle ways.

Stock photos are fine as long as they don't seem obviously stock.

Should not have
• Nothing buddha like. Nothing themed. It should be all inclusive and not seek to identify with any particular group or gender.

Nothing that fits the stereotype of "Miami Beach." We want to represent ourselves in the same category as the best spas in the world because we moving everything we do in that direction. Think class!

```html
<!DOCTYPE html>
<html lang="en">
<head>
<meta charset="utf-8">
<title>Thornbury Spa – Service Price List</title>
<link rel="stylesheet" href="https://fonts.googleapis.com/css2?family=Questrial&display=swap">
<style>
  :root {
    --bg-center: #4a4a4c;
    --bg-edge: #161617;
    --band-light: #5a5a5c;
    --band-dark: #2e2e30;
    --text: #f2f2f2;
    --text-soft: #e4e4e4;
    --rule: rgba(255, 255, 255, 0.32);
    --hair-red: #b5362c;
    --nails-violet: #9a5aa8;
    --massage-plum: #6b1e3c;
    --url-grey: #c9c9c9;
  }
  * { box-sizing: border-box; margin: 0; padding: 0; }
  html, body { width: 1200px; height: 874px; overflow: hidden; background: var(--bg-edge); }
  body { font-family: "Questrial", "Century Gothic", sans-serif; color: var(--text); }

  .price-sheet {
    position: relative;
    width: 1200px;
    height: 874px;
    overflow: hidden;
    background: radial-gradient(ellipse 70% 75% at 50% 42%, var(--bg-center) 0%, #2f2f31 55%, var(--bg-edge) 100%);
  }
  .footer-band {
    position: absolute;
    left: 0; right: 0; bottom: 0;
    height: 104px;
    background: linear-gradient(180deg, var(--band-light) 0%, #4a4a4c 40%, var(--band-dark) 100%);
    clip-path: polygon(0 22%, 100% 0, 100% 100%, 0 100%);
  }
  .website {
    position: absolute;
    left: 0; right: 0; top: 812px;
    text-align: center;
    font-size: 29px;
    letter-spacing: 11px;
    color: var(--url-grey);
  }

  .brand {
    position: absolute;
    left: 40px; top: 52px;
    width: 340px;
    text-align: center;
  }
  .brand-mark { display: block; margin: 0 auto 22px; }
  .brand-name {
    font-size: 31px;
    letter-spacing: 3px;
    color: var(--text);
    text-transform: uppercase;
    white-space: nowrap;
  }

  .menu-banner {
    position: absolute;
    width: 340px;
    height: 25px;
    line-height: 25px;
    text-align: center;
    font-size: 19px;
    color: var(--text);
    text-transform: uppercase;
  }
  .menu-banner.hair { left: 40px; top: 268px; background: var(--hair-red); }
  .menu-banner.nails { left: 431px; top: 189px; background: var(--nails-violet); }
  .menu-banner.massage { left: 810px; top: 371px; background: var(--massage-plum); }

  .service-group { position: absolute; width: 340px; }
  .col-left { left: 40px; }
  .col-middle { left: 430px; }
  .col-right { left: 810px; }

  .group-head, .service-row {
    display: grid;
    grid-template-columns: minmax(0, 1fr) 90px 82px;
    align-items: center;
  }
  .col-middle .group-head, .col-middle .service-row { grid-template-columns: minmax(0, 1fr) 70px 82px; }
  .col-right .group-head, .col-right .service-row { grid-template-columns: minmax(0, 1fr) 60px 82px; }

  .group-head {
    height: 24px;
    margin-bottom: 1px;
    font-size: 18px;
    border-top: 1px solid var(--rule);
    border-right: 1px solid var(--rule);
    border-bottom: 1px solid var(--rule);
  }
  .group-head > span:first-child { white-space: nowrap; }
  .group-head.open { border: none; }
  .group-head .price-col { font-size: 17px; }

  .service-row {
    height: 25.3px;
    font-size: 12.8px;
    letter-spacing: -0.15px;
    color: var(--text-soft);
  }
  .price-col { text-align: right; white-space: nowrap; }
  .service-name { white-space: nowrap; }
  .service-row.compact .service-name { font-size: 11.8px; letter-spacing: -0.4px; }
  .service-row.compact .service-name.fine { font-size: 10.6px; letter-spacing: -0.5px; }
  .service-row.tall {
    height: 39px;
    align-items: end;
    padding-bottom: 4px;
  }
  .service-row.tall .service-name { line-height: 14px; white-space: normal; }
</style>
</head>
<body>
<main class="price-sheet">

  <header class="brand">
    <svg class="brand-mark" width="70" height="70" viewBox="0 0 70 70" aria-hidden="true">
      <circle cx="35" cy="35" r="33" fill="none" stroke="#f2f2f2" stroke-width="2.5"/>
    </svg>
    <div class="brand-name">Thornbury Spa</div>
  </header>

  <!-- Hair -->
  <div class="menu-banner hair">Hair Menu</div>

  <section class="service-group col-left" style="top:305px">
    <div class="group-head"><span>Cutting</span><span class="price-col">LP</span><span class="price-col">HG</span></div>
    <div class="service-row"><span class="service-name">men's hair cut</span><span class="price-col">from $29</span><span class="price-col">from $35</span></div>
    <div class="service-row"><span class="service-name">women's wet cut</span><span class="price-col">from $49</span><span class="price-col">from $60</span></div>
    <div class="service-row"><span class="service-name">women's cut &amp; blowout</span><span class="price-col">from $69</span><span class="price-col">from $80</span></div>
  </section>

  <section class="service-group col-left" style="top:411px">
    <div class="group-head"><span>Coloring</span><span class="price-col">LP</span><span class="price-col">HG</span></div>
    <div class="service-row"><span class="service-name">ingle process</span><span class="price-col">from $55</span><span class="price-col">from $65</span></div>
    <div class="service-row compact"><span class="service-name">partial highlights/lowlights</span><span class="price-col">from $99</span><span class="price-col">from $120</span></div>
    <div class="service-row"><span class="service-name">full highlights/lowlights</span><span class="price-col">from $149</span><span class="price-col">from $180</span></div>
    <div class="service-row"><span class="service-name">double process</span><span class="price-col">from $99</span><span class="price-col">from $110</span></div>
  </section>

  <section class="service-group col-left" style="top:542px">
    <div class="group-head"><span>Extensions</span><span class="price-col">LP</span><span class="price-col">HG</span></div>
    <div class="service-row compact"><span class="service-name">hair extensions by silkline</span><span class="price-col">from $799</span><span class="price-col">from $950</span></div>
    <div class="service-row"><span class="service-name">extensions repair</span><span class="price-col">from $249</span><span class="price-col">from $300</span></div>
    <div class="service-row"><span class="service-name">extensions removal</span><span class="price-col">from $59</span><span class="price-col">from $70</span></div>
  </section>

  <section class="service-group col-left" style="top:648px">
    <div class="group-head"><span>Treatments</span><span class="price-col">LP</span><span class="price-col">HG</span></div>
    <div class="service-row tall"><span class="service-name">scalp massage +<br>nourishing treatment</span><span class="price-col">from $19</span><span class="price-col">from $25</span></div>
    <div class="service-row tall"><span class="service-name">ultra conditioning<br>reconstructor</span><span class="price-col">from $29</span><span class="price-col">from $35</span></div>
    <div class="service-row"><span class="service-name">keratin by veranti treatment</span><span class="price-col">from $199</span><span class="price-col">from $250</span></div>
  </section>

  <!-- Styling & Nails -->
  <section class="service-group col-middle" style="top:25px">
    <div class="group-head"><span>Styling</span><span class="price-col">LP</span><span class="price-col">HG</span></div>
    <div class="service-row"><span class="service-name">wet head blowout</span><span class="price-col">from $25</span><span class="price-col">from $30</span></div>
    <div class="service-row"><span class="service-name">shampoo &amp; blowout</span><span class="price-col">from $35</span><span class="price-col">from $40</span></div>
    <div class="service-row"><span class="service-name">updos or styling</span><span class="price-col">from $49</span><span class="price-col">from $80</span></div>
    <div class="service-row"><span class="service-name">wedding hair trials</span><span class="price-col">from $89</span><span class="price-col"></span></div>
    <div class="service-row"><span class="service-name">wedding day hair</span><span class="price-col">from $49</span><span class="price-col"></span></div>
  </section>

  <div class="menu-banner nails">Nails Menu</div>

  <section class="service-group col-middle" style="top:226px">
    <div class="group-head"><span>Nail Bar Polishing</span><span class="price-col">LP</span><span class="price-col">HG</span></div>
    <div class="service-row"><span class="service-name">Hand Polish Change</span><span class="price-col">$10</span><span class="price-col">$12</span></div>
    <div class="service-row"><span class="service-name">Foot Polish Change</span><span class="price-col">$12</span><span class="price-col">$13</span></div>
    <div class="service-row"><span class="service-name">Polish Combination</span><span class="price-col">$19</span><span class="price-col">$25</span></div>
  </section>

  <section class="service-group col-middle" style="top:332px">
    <div class="group-head"><span>The Classic</span><span class="price-col">LP</span><span class="price-col">HG</span></div>
    <div class="service-row"><span class="service-name">The Classic Manicure</span><span class="price-col">$19</span><span class="price-col">$23</span></div>
    <div class="service-row"><span class="service-name">The Classic Pedicure</span><span class="price-col">$34</span><span class="price-col">$40</span></div>
    <div class="service-row"><span class="service-name">The Classic Combination</span><span class="price-col">$49</span><span class="price-col">$60</span></div>
  </section>

  <section class="service-group col-middle" style="top:438px">
    <div class="group-head"><span>The Ultimate</span><span class="price-col">LP</span><span class="price-col">HG</span></div>
    <div class="service-row compact"><span class="service-name">The Ultimate Manicure</span><span class="price-col">$29</span><span class="price-col">$35</span></div>
    <div class="service-row compact"><span class="service-name">The Ultimate Pedicure</span><span class="price-col">$49</span><span class="price-col">$50</span></div>
    <div class="service-row compact"><span class="service-name">The Ultimate Combination</span><span class="price-col">$69</span><span class="price-col">$80</span></div>
  </section>

  <section class="service-group col-middle" style="top:544px">
    <div class="group-head"><span>Gelara</span><span class="price-col">LP</span><span class="price-col">HG</span></div>
    <div class="service-row"><span class="service-name">Gelara Manicure</span><span class="price-col">$39</span><span class="price-col">$45</span></div>
    <div class="service-row"><span class="service-name">Gelara Pedicure</span><span class="price-col">$59</span><span class="price-col">$70</span></div>
    <div class="service-row"><span class="service-name">Gelara Combination</span><span class="price-col">$89</span><span class="price-col">$115</span></div>
    <div class="service-row"><span class="service-name">Gelara Removal</span><span class="price-col">$10</span><span class="price-col">$10</span></div>
  </section>

  <section class="service-group col-middle" style="top:676px">
    <div class="group-head open"><span>The Express</span><span class="price-col">LP</span><span class="price-col">HG</span></div>
    <div class="service-row"><span class="service-name">The 15-Minute Express Manicure</span><span class="price-col">$15</span><span class="price-col">$18</span></div>
    <div class="service-row"><span class="service-name">The 30-Minute Express Pedicure</span><span class="price-col">$25</span><span class="price-col">$30</span></div>
    <div class="service-row"><span class="service-name">The 45-Minute Express Combination</span><span class="price-col">$39</span><span class="price-col">$45</span></div>
  </section>

  <!-- Overlays, Charges & Massage -->
  <section class="service-group col-right" style="top:25px">
    <div class="group-head"><span>Natural Nail Overlays</span><span class="price-col">LP</span><span class="price-col">HG</span></div>
    <div class="service-row"><span class="service-name">Acrylics Full Set</span><span class="price-col">$49</span><span class="price-col">$60</span></div>
    <div class="service-row"><span class="service-name">Acrylic Fills</span><span class="price-col">$29</span><span class="price-col">$35</span></div>
    <div class="service-row"><span class="service-name">Traditional Gel Full Set</span><span class="price-col">$59</span><span class="price-col">$70</span></div>
    <div class="service-row"><span class="service-name">Traditional Gel Fills</span><span class="price-col">$39</span><span class="price-col">$35</span></div>
    <div class="service-row"><span class="service-name">Pink &amp; White Full Set</span><span class="price-col">$59</span><span class="price-col">$70</span></div>
    <div class="service-row"><span class="service-name">Pink &amp; White Fills</span><span class="price-col">$39</span><span class="price-col">$45</span></div>
  </section>

  <section class="service-group col-right" style="top:207px">
    <div class="group-head"><span>Additional Charges</span><span class="price-col">LP</span><span class="price-col">HG</span></div>
    <div class="service-row compact"><span class="service-name">Nail Repair</span><span class="price-col">$5</span><span class="price-col">$5</span></div>
    <div class="service-row compact"><span class="service-name fine">Artificial Nail Removal (removal only)</span><span class="price-col">$29</span><span class="price-col">$35</span></div>
    <div class="service-row compact"><span class="service-name fine">Artificial Nail Removal (with other new service)</span><span class="price-col">$19</span><span class="price-col">$25</span></div>
    <div class="service-row compact"><span class="service-name">Gelara Removal</span><span class="price-col">$10</span><span class="price-col">$10</span></div>
    <div class="service-row compact"><span class="service-name">Callus Removal</span><span class="price-col">$10</span><span class="price-col">$10</span></div>
  </section>

  <div class="menu-banner massage">Massage Menu</div>

  <section class="service-group col-right" style="top:413px">
    <div class="group-head"><span>Swedish Massage</span><span class="price-col">LP</span><span class="price-col">HG</span></div>
    <div class="service-row"><span class="service-name">The 30-Minute Swedish</span><span class="price-col">$59</span><span class="price-col">$70</span></div>
    <div class="service-row"><span class="service-name">The 60-Minute Swedish</span><span class="price-col">$89</span><span class="price-col">$105</span></div>
    <div class="service-row"><span class="service-name">The 90-Minute Swedish</span><span class="price-col">$129</span><span class="price-col">$150</span></div>
    <div class="service-row"><span class="service-name">The 120-Minute Swedish</span><span class="price-col">$169</span><span class="price-col">$225</span></div>
  </section>

  <section class="service-group col-right" style="top:545px">
    <div class="group-head"><span>Deep Tissue Massage</span><span class="price-col">LP</span><span class="price-col">HG</span></div>
    <div class="service-row"><span class="service-name">The 30-Minute Deep Tissue</span><span class="price-col">$69</span><span class="price-col">$80</span></div>
    <div class="service-row"><span class="service-name">The 60-Minute Deep Tissue</span><span class="price-col">$99</span><span class="price-col">$120</span></div>
    <div class="service-row"><span class="service-name">The 90-Minute Deep Tissue</span><span class="price-col">$139</span><span class="price-col">$180</span></div>
    <div class="service-row"><span class="service-name">The 120-Minute Deep Tissue</span><span class="price-col">$189</span><span class="price-col">$240</span></div>
  </section>

  <section class="service-group col-right" style="top:677px">
    <div class="group-head"><span>Sports - Specific Massage</span><span class="price-col">LP</span><span class="price-col">HG</span></div>
    <div class="service-row"><span class="service-name">The 30-Minute Tune-up</span><span class="price-col">$69</span><span class="price-col">$80</span></div>
    <div class="service-row"><span class="service-name">The 45-Minute Overhaul</span><span class="price-col">$89</span><span class="price-col">$105</span></div>
  </section>

  <footer>
    <div class="footer-band"></div>
    <div class="website">www.velloraspa-studio.com</div>
  </footer>

</main>
</body>
</html>
```